Simple and clean

We need a business card design for a new company called Dwelling Hawk. It is a search engine to find current properties for sale or rent in New Zealand market.
We have already a colour scheme that we would like people to use.
Light brown: #D4CCB0
Light green: #D6E4D4
Green: #669966
Black/White
It is OK to divert from this colour scheme slightly as long as there is a green component to the business card.
Final design should be clean, simple and should communicate the nature of the business.
Target Market(s)
- First home buyers
- Real estate agents
- People seeking rentals
Industry/Entity Type
Business
Requirements
Must have
- Use those or similar colours.
Light brown: #D4CCB0
Light green: #D6E4D4
Green: #669966
Black/White

```html
<!DOCTYPE html>
<html lang="en">
<head>
<meta charset="UTF-8">
<title>Dwelling Hawk — Business Card</title>
<link rel="stylesheet" href="https://fonts.googleapis.com/css2?family=Josefin+Sans:wght@300&family=Open+Sans:wght@300;700&display=swap">
<style>
  :root {
    --backdrop: #141414;
    --card-white: #ffffff;
    --card-white-shade: #ebebeb;
    --brand-green: #689a66;
    --brand-green-dark: #5f8f5d;
    --ink: #151515;
    --card-text: #eef3ec;
    --card-text-soft: #dfe9dc;
  }
  * { box-sizing: border-box; margin: 0; padding: 0; }
  html, body {
    width: 1200px;
    height: 851px;
    overflow: hidden;
  }
  body {
    background: radial-gradient(ellipse at 50% 30%, #262626 0%, var(--backdrop) 70%);
    font-family: "Open Sans", Arial, sans-serif;
    position: relative;
  }
  .card {
    position: absolute;
    left: 120px;
    top: 153px;
    width: 960px;
    height: 545px;
    border-radius: 26px;
    overflow: hidden;
    background: var(--brand-green);
  }
  .card__header {
    position: absolute;
    left: 0; top: 0;
    width: 100%;
    height: 212px;
    background: linear-gradient(180deg, var(--card-white) 0%, var(--card-white) 55%, var(--card-white-shade) 100%);
    display: flex;
    align-items: center;
    justify-content: center;
    gap: 16px;
  }
  .brand__dot {
    width: 46px;
    height: 46px;
    border-radius: 50%;
    background: var(--brand-green);
  }
  .brand__name {
    font-family: "Open Sans", Arial, sans-serif;
    font-weight: 700;
    font-size: 56px;
    color: var(--ink);
    letter-spacing: -0.5px;
  }
  .card__body {
    position: absolute;
    left: 0; top: 212px;
    width: 100%;
    height: 333px;
    background: linear-gradient(180deg, var(--brand-green) 0%, var(--brand-green-dark) 100%);
  }
  .person {
    position: absolute;
    left: 0; top: 50px;
    width: 100%;
    text-align: center;
    font-family: "Josefin Sans", Arial, sans-serif;
    font-weight: 300;
    color: var(--card-text);
  }
  .person__name {
    font-size: 52px;
    line-height: 1.1;
    padding-right: 20px;
  }
  .person__role {
    font-size: 21px;
    letter-spacing: 0.28em;
    color: var(--card-text-soft);
    margin-top: 6px;
    padding-right: 20px;
  }
  .contact {
    position: absolute;
    left: 0; bottom: 64px;
    width: 100%;
    text-align: center;
    font-size: 19px;
    font-weight: 300;
    color: var(--card-text);
    white-space: nowrap;
  }
  .contact__label { font-weight: 700; }
  .contact__sep { margin: 0 6px; }
</style>
</head>
<body>
  <div class="card">
    <header class="card__header">
      <span class="brand__dot"></span>
      <span class="brand__name">Dwelling Hawk</span>
    </header>
    <section class="card__body">
      <div class="person">
        <div class="person__name">Alex Carter</div>
        <div class="person__role">director</div>
      </div>
      <p class="contact">
        <span class="contact__label">mobile</span> 021 - 555 - 019<span class="contact__sep">|</span><span class="contact__label">email</span> mail@dwellinghawk.com<span class="contact__sep">|</span><span class="contact__label">web</span> www.dwellinghawk.co.nz
      </p>
    </section>
  </div>
</body>
</html>
```